Need a cover for eBook:
Title is: 52 Blunders That Sink Your Indie-Released eBook.
Remarks about the title: I know that is difficult to design a cover with a number. You can add the word TOP (in caps or not) before 69 mistakes. It is not mandatory to insert the word TOP. It is up to you if you think you can create a better cover.
Subtitle is: A Starter's Handbook for Releasing Solo, Arranging Pictures and Words, Planning Pages, Raising Signups and Moving More Copies
Author: Walter P. Brenshaw
Publisher: Quillmark Works
The book made the presentation of errors that can occur during the production of an ebook. Title must be big, the title should be readable even when the image is reduced in size. No photo please.
I join my projects as an example. Do what you want but I need impact.

Target Market(s)

Book to sell first at Borvela Reader Shop. Target is authors, men or women, who want to produce ebooks.

Industry/Entity Type

Publishing Company

Font styles to use
Sans Serif

Colors
3176b5
9bcb3c

Requirements
Must have
• High readability when cover is small.
• Here is the definition of the word KILL
• put an end to or cause the failure or defeat of (something).
• "the committee voted to kill the project"
• synonyms: destroy, put an end to, end, extinguish, dash, quash, ruin, wreck, shatter, smash, crush, scotch, thwart; informalput the kibosh on, stymie, scuttle
• "this would kill all hopes of progress"
• veto, defeat, vote down, rule against, reject, throw out, overrule, overturn, put a stop to, quash, squash
• "an opposition attempt to kill the bill"
Nice to have
• I suggested 2 colors but you can you use another one or two. I want cover that sell. There is so bright ideas here. Come on down!
Should not have
• No picture or photo. If a photo or an object had power to the cover, you can insert one. I don't want a photo-collage.

```html
<!DOCTYPE html>
<html lang="en">
<head>
<meta charset="utf-8">
<title>52 Blunders That Sink Your Indie-Released eBook</title>
<link rel="stylesheet" href="https://fonts.googleapis.com/css2?family=Saira+Condensed:wght@600;700;800&display=swap">
<style>
  :root {
    --lime: #99ff00;
    --aqua: #00ffff;
    --ink: #000000;
    --paper: #ffffff;
    --mist: #e6e6e6;
    --title-green: #a6f20d;
  }
  html, body {
    margin: 0;
    padding: 0;
    overflow: hidden;
    background: var(--paper);
  }
  .cover {
    position: relative;
    width: 749px;
    height: 1200px;
    overflow: hidden;
    background: var(--lime);
    font-family: "Saira Condensed", "Arial Narrow", sans-serif;
    text-align: center;
  }
  .author {
    position: absolute;
    top: 22px;
    left: 0;
    width: 100%;
    margin: 0;
    font-weight: 700;
    font-size: 64px;
    line-height: 1;
    letter-spacing: 0.5px;
    color: var(--ink);
  }
  .author-surname { color: var(--mist); }
  .feature-art {
    position: absolute;
    left: 180px;
    top: 150px;
    width: 420px;
    height: 490px;
    background: var(--ink);
  }
  .water {
    position: absolute;
    left: 0;
    top: 600px;
    width: 749px;
    height: 600px;
  }
  .big-number {
    position: absolute;
    top: 228px;
    left: 0;
    width: 100%;
    margin: 0;
    font-weight: 800;
    font-size: 360px;
    line-height: 1;
    letter-spacing: -6px;
    color: var(--paper);
  }
  .title {
    position: absolute;
    top: 664px;
    left: 0;
    width: 100%;
    margin: 0;
  }
  .title-main {
    display: block;
    font-weight: 700;
    font-size: 134px;
    line-height: 1;
    letter-spacing: 2px;
    color: var(--paper);
  }
  .title-rest {
    display: block;
    margin-top: 6px;
    font-weight: 700;
    font-size: 66px;
    line-height: 60px;
    color: var(--title-green);
  }
  .subtitle {
    position: absolute;
    top: 944px;
    left: 0;
    width: 100%;
    margin: 0;
    font-weight: 600;
    font-size: 26px;
    line-height: 40px;
    color: var(--ink);
  }
  .subtitle span { display: block; }
  .publisher {
    position: absolute;
    top: 1096px;
    left: 0;
    width: 100%;
    margin: 0;
    font-weight: 700;
    font-size: 60px;
    line-height: 1;
    color: var(--ink);
  }
  .publisher-first { color: var(--paper); }
</style>
</head>
<body>
  <main class="cover">
    <p class="author"><span>Walter</span> <span class="author-surname">P. Brenshaw</span></p>

    <div class="feature-art" role="img" aria-label="Illustration area: dark figure sinking into water"></div>

    <svg class="water" viewBox="0 0 749 600" aria-hidden="true">
      <path fill="var(--aqua)" d="M0 20 C 60 0, 120 0, 180 14 C 250 30, 300 34, 370 18 C 440 2, 500 2, 560 16 C 630 32, 690 30, 749 10 L 749 600 L 0 600 Z"/>
    </svg>

    <p class="big-number">52</p>

    <h1 class="title">
      <span class="title-main">BLUNDERS</span>
      <span class="title-rest">THAT SINK YOUR INDIE<br>RELEASED EBOOK</span>
    </h1>

    <p class="subtitle">
      <span>A Starter's Handbook for Releasing Solo, Arranging</span>
      <span>Pictures and Words, Planning Pages, Raising Signups</span>
      <span>and Moving More Copies</span>
    </p>

    <p class="publisher"><span class="publisher-first">Quillmark</span> Works</p>
  </main>
</body>
</html>
```